GJ & DW Fencing Pty Ltd

We already have an existing logo created by Pixel Harbour however we have restructured to a company. We would like someone to add Pty Ltd to our business name please.

Colors

Designer to choose only greyscale colors for use in the design.

```html
<!DOCTYPE html>
<html lang="en">
<head>
<meta charset="utf-8">
<title>GJ &amp; DW Fencing Pty Ltd — Business Card</title>
<link rel="stylesheet" href="https://fonts.googleapis.com/css2?family=Lato:wght@400;700&family=Merriweather:wght@700;900&display=swap">
<style>
  :root {
    --backdrop: #2b2b2c;
    --card: #1f2022;
    --card-edge: #2a2b2d;
    --texture-light: #242527;
    --texture-dark: #1a1b1d;
    --ink: #ffffff;
    --ink-soft: #d9d9d9;
    --rule: #6a6a6c;
    --icon-fg: #1f2022;
  }
  * { box-sizing: border-box; margin: 0; padding: 0; }
  html, body {
    width: 1200px; height: 1108px; overflow: hidden;
    background: var(--backdrop);
  }
  .stage {
    position: relative; width: 1200px; height: 1108px;
    display: flex; justify-content: center; align-items: center; gap: 60px;
  }
  .card {
    width: 480px; height: 740px;
    background: var(--card);
    border-radius: 28px;
    box-shadow: 0 18px 40px rgba(0,0,0,.45), inset 0 0 0 1px var(--card-edge);
    position: relative;
    overflow: hidden;
  }
  .card--front {
    display: flex; flex-direction: column; align-items: center;
    padding-top: 150px; color: var(--ink);
  }
  .brand {
    display: flex; align-items: center; gap: 12px;
    font-family: "Merriweather", Georgia, serif;
    font-weight: 900; font-size: 27px; letter-spacing: .3px;
    color: var(--ink); text-align: center;
  }
  .brand__mark {
    width: 22px; height: 22px; border-radius: 50%; background: var(--ink); flex: none;
  }
  .holder {
    margin-top: 190px;
    font-family: "Merriweather", Georgia, serif;
    font-weight: 700; font-size: 20px; letter-spacing: .6px;
    text-transform: uppercase;
  }
  .contacts { margin-top: 22px; width: 100%; display: flex; flex-direction: column; align-items: center; }
  .contact { display: flex; flex-direction: column; align-items: center; }
  .contact__divider { display: flex; align-items: center; gap: 10px; margin-bottom: 8px; }
  .contact__rule { width: 58px; height: 1px; background: var(--rule); }
  .contact__icon { width: 28px; height: 28px; display: block; }
  .contact__text {
    font-family: "Lato", Arial, sans-serif; font-size: 20px; color: var(--ink-soft);
    margin-bottom: 10px; letter-spacing: .2px;
  }

  .back__texture {
    position: absolute; inset: 0;
    background: radial-gradient(ellipse at 50% 45%, var(--texture-light) 0%, var(--card) 55%, var(--texture-dark) 100%);
  }
  .back__brand {
    position: absolute; left: 300px; top: 575px; transform: translate(-50%, -50%);
    display: flex; align-items: center; gap: 8px;
    font-family: "Merriweather", Georgia, serif;
    font-weight: 900; font-size: 13px; color: var(--ink); white-space: nowrap;
  }
  .back__mark { width: 14px; height: 14px; border-radius: 50%; background: var(--ink); flex: none; }
</style>
</head>
<body>
<main class="stage">
  <section class="card card--front" aria-label="Card front">
    <div class="brand"><span class="brand__mark"></span><span>GJ &amp; DW Fencing Pty Ltd</span></div>

    <p class="holder">Tom Harrowfield</p>

    <div class="contacts">
      <div class="contact">
        <div class="contact__divider">
          <span class="contact__rule"></span>
          <svg class="contact__icon" viewBox="0 0 28 28" aria-hidden="true">
            <circle cx="14" cy="14" r="14" fill="#fff"/>
            <path d="M9 8.5c.6-.6 1.5-.6 2 0l1.6 1.9c.4.5.4 1.2-.1 1.7l-.9.9c.8 1.7 2 2.9 3.6 3.7l.9-.9c.5-.5 1.2-.5 1.7-.1l1.9 1.6c.6.5.6 1.4 0 2l-1 1c-.9.9-2.3 1.1-3.4.5-3-1.6-5.3-3.9-6.9-6.9-.6-1.1-.4-2.5.5-3.4z" fill="var(--icon-fg)"/>
          </svg>
          <span class="contact__rule"></span>
        </div>
        <p class="contact__text">044 5182907</p>
      </div>

      <div class="contact">
        <div class="contact__divider">
          <span class="contact__rule"></span>
          <svg class="contact__icon" viewBox="0 0 28 28" aria-hidden="true">
            <circle cx="14" cy="14" r="14" fill="#fff"/>
            <rect x="7.5" y="9.5" width="13" height="9" rx="1" fill="var(--icon-fg)"/>
            <path d="M8 10.2l6 4.6 6-4.6" fill="none" stroke="#fff" stroke-width="1.1"/>
          </svg>
          <span class="contact__rule"></span>
        </div>
        <p class="contact__text">gjdwfencing@mailbox.com</p>
      </div>

      <div class="contact">
        <div class="contact__divider">
          <span class="contact__rule"></span>
          <svg class="contact__icon" viewBox="0 0 28 28" aria-hidden="true">
            <circle cx="14" cy="14" r="14" fill="#fff"/>
            <path d="M14 6.5a5 5 0 0 0-5 5c0 3.7 5 9.5 5 9.5s5-5.8 5-9.5a5 5 0 0 0-5-5z" fill="var(--icon-fg)"/>
            <circle cx="14" cy="11.5" r="1.9" fill="#fff"/>
          </svg>
          <span class="contact__rule"></span>
        </div>
        <p class="contact__text">PO Box 418 Ashvale WA 6412</p>
      </div>
    </div>
  </section>

  <section class="card card--back" aria-label="Card back">
    <div class="back__texture" role="img" aria-label="Faint repeating tonal pattern of the company emblem across the card back"></div>
    <div class="back__brand"><span class="back__mark"></span><span>GJ &amp; DW Fencing Pty Ltd</span></div>
  </section>
</main>
</body>
</html>
```